KTMR Website and Inner page template

Home page website design with inner page design for template. Details below as well as in txt document included
Project Description: New website for a current client ( KTMR ) .. current website is located at https://www.ktmr-board.org/Home.aspx
I need a home page design with an inner page design that will be used as a template ( 2 pages )
Logo is attached
Important notes:
Every page has to include the mission and vision. See below
"Our mission: to protect the public by promoting excellence in chiropractic regulation through service to our member boards
Our vision: The KTMR is the premier international resource for information and consolidated services for ensuring the safe, ethical practice of chiropractic"
Social media icons on the head of every page
facebook
twitter
linkedin
instagram
youtube
Every page needs to include the phone number on the header and footer
Main navigation links ( they are going to be different from current website ). Since most of these links are going to have sub-menus, please show the rollover affect. I have included the sub-menu options for "Get Started". The sub-menu should not be in a "list style" because the sub-menu links are categorized in some cases. A good example on their current website is to roll over the "Services" link in the main navigation
"Get Started" Sub-menu options ( categories and links )
- Chiropractic Regulators
- Annual Meeting
- District Meetings
- Licensing Board Information
- Library
- Administrators ( DRVOM )
- Legal Advisors ( DRVOM )
- Other Chiropractic Organizations
- Chiropractic Patients
- How to check a license
- Look up a license
- Request a Disciplinary Report
- Consumer Information
- Registered Chiropractors & Chiropractic Assistants
- Continuing Education Courses
- Chiropractic Assistant
- Certification
- View your continuing Ed Credits
Full list if primary navigation links:
Home
Contact
Company Info
Chiropractic Boards
Resources
Services
Get Started
Home Page Specifics:
"Hero Banner" or large "Slider" image with text at top of page below main navigation
4 primary points of interest to highlight
- TEP-ROW ( therapist event portal registry of warnings )
- ROVE ( Registry of Vetted Ongoing Learning )
- MSDV ( Member Spinal Desk Volunteers )
- Lanternway ( Open Ledger of Practitioner Standing )
Large "Member Access" area with the following links inside it
- Register for meetings
- Pay an Invoice
- TEP-ROW
- ROVE
- MSDV
- Report to TEP-ROW
- DRVOM Login
Large "Get Started" section with 3 categories that have links
- Chiropractic Regulators
- Annual Meeting
- District Meetings
- Library
- Chiropractic Patients
- How to Check a license
- Look up a license
- Consumer Information
- Coninuing Education Courses
- Chiropractic Assistant
- Certification
- View Your Continuing Ed Credits
Inner page specifics:
The inner page should look similar to the home page at the header and footer areas then have a large area for content. No large images or anything like that needed..
IMPORTANT... ONLY USE GRAPHICS/IMAGES from pixmeadow. ( https://www.pixmeadowimages.com/ ) This is important because we have an account with them so you can use the watermarked images then when I build the website I can easily purchase the licensing rights for those images. You dont' need an account to do searches, locate images and use the water marked image in the design.
Target Market(s)
Chiropractic Licensing
Number of Pages Required
2 page
Requirements
Must have
- Please see attached document
Nice to have
Should not have

```html
<!DOCTYPE html>
<html lang="en">
<head>
<meta charset="utf-8">
<title>KTMR – Home page and Get Started menu</title>
<link href="https://fonts.googleapis.com/css2?family=Roboto:wght@300;400;500;700&display=swap" rel="stylesheet">
<style>
:root{
  --blue:#2b5ca8;
  --blue-dark:#1f4a8e;
  --ink:#222;
  --text:#666;
  --muted:#888;
  --line:#e2e4e8;
  --section:#f1f2f4;
  --stage:#dcdcdc;
  --white:#fff;
}
*{box-sizing:border-box;margin:0;padding:0}
html,body{width:1137px;height:1200px;overflow:hidden}
body{background:var(--stage);font-family:'Roboto',sans-serif;position:relative}
.screen{position:absolute;top:45px;width:876px;height:1829px;background:var(--white);transform:scale(.606);transform-origin:0 0;overflow:hidden;box-shadow:0 0 6px rgba(0,0,0,.15)}
.screen--home{left:24px}
.screen--menu{left:582px}
.abs{position:absolute}

/* header */
.brand{left:51px;top:13px;display:flex;align-items:center;gap:6px}
.brand__mark{width:42px;height:42px;background:var(--blue)}
.brand__name{font-size:17px;line-height:15px;color:var(--blue-dark);font-weight:400;width:130px}
.topbar{top:11px;font-size:11px;color:#444;display:flex;align-items:center;gap:4px}
.topbar b{font-weight:400;font-size:13px}
.topbar svg{width:14px;height:14px}
.topbar--email{left:359px}
.topbar--call{left:524px}
.get-started-btn{left:700px;top:3px;width:94px;height:28px;font-size:11px;font-weight:700;color:#222;display:flex;align-items:center;justify-content:center;gap:4px}
.get-started-btn.is-open{background:var(--blue);color:var(--white)}
.header-rule{left:286px;top:35px;width:510px;height:1px;background:var(--line)}
.nav{left:307px;top:47px;display:flex;font-size:10px;color:#333}
.nav span{padding:0 9px;border-left:1px solid #555;line-height:11px}
.nav span:first-child{border:0;padding-left:0;color:var(--blue)}

/* hero */
.hero{left:0;top:70px}
.hero__dot{left:823px;width:10px;height:10px;border-radius:50%;border:1.5px solid var(--white)}
.hero__dot.is-active{background:var(--white)}
.hero__title{left:232px;top:470px;color:var(--white);font-size:33px;font-weight:700}
.hero__sub{left:232px;top:508px;color:var(--white);font-size:19px;font-weight:400}
.hero__cta{left:551px;top:485px;width:120px;height:38px;background:var(--white);color:var(--blue);font-size:12px;font-weight:500;display:flex;align-items:center;justify-content:center}

/* dropdown */
.mega{left:225px;top:48px;width:587px;height:259px;background:var(--blue);display:flex;padding:37px 0 0 17px;font-size:11px;color:var(--white);line-height:22.5px}
.mega::before{content:"";position:absolute;top:-7px;left:560px;border:7px solid transparent;border-top:0;border-bottom-color:var(--blue)}
.mega ul{list-style:none}
.mega li::before{content:"» "}
.mega__col1{width:196px}.mega__col2{width:185px}.mega__col3{width:180px}
.mega__indent{padding-left:10px}
.mega__indent::before{content:""!important}

/* mission */
.mission__frame{left:69px;top:605px;width:172px;height:135px;background:var(--blue)}
.mission__photo{left:82px;top:618px;width:332px;height:275px;background:linear-gradient(135deg,#d9dcdf,#9aa0a6 55%,#5c6168);box-shadow:0 4px 10px rgba(0,0,0,.2)}
.point__icon{left:439px;width:40px;height:40px;border-radius:50%;background:var(--blue)}
.point__title{left:490px;font-size:24px;font-weight:700;color:var(--ink)}
.point__text{left:491px;width:310px;font-size:12px;line-height:21px;color:var(--text)}

/* quicklinks */
.section-title{left:0;width:876px;top:953px;text-align:center;font-size:22px;font-weight:700;color:var(--ink)}
.quick{top:1043px;width:231px;height:171px;background:var(--white);box-shadow:0 0 5px rgba(0,0,0,.15)}
.quick__inner{position:absolute;inset:8px;border:1px dashed #ccc;text-align:center;padding:68px 12px 0}
.quick__badge{top:-42px;left:73px;width:86px;height:98px}
.quick__name{font-size:11px;line-height:18px;color:var(--blue-dark);text-decoration:underline}
.quick__desc{font-size:11px;line-height:17px;color:var(--muted);margin-top:0}
.arrow{top:1103px;width:16px;height:32px}

/* member area */
.members{left:0;top:1278px;width:876px;height:420px;background:var(--section)}
.h-blue{font-size:24px;font-weight:700;color:var(--blue)}
.member-list{left:69px;top:1350px;font-size:12px;color:#333;line-height:17.5px}
.member-list a{color:var(--blue);text-decoration:underline;display:block;margin-top:14px}
.member-list li{list-style:none;line-height:23px}
.divider{left:272px;top:1320px;width:1px;height:270px;background:#ddd}
.gs-card{top:1365px;width:171px;height:220px;background:var(--white);box-shadow:0 0 4px rgba(0,0,0,.08);padding:14px 10px 0 11px}
.gs-card__head{display:flex;align-items:center;gap:6px;font-size:13px;font-weight:500;color:#222;margin-bottom:14px}
.gs-card__head svg{width:24px;height:24px}
.gs-card ul{list-style:none;font-size:10.5px;color:#555;line-height:20.6px;padding-left:4px}
.gs-card a{color:var(--blue);text-decoration:underline}

/* footer */
.footer{left:0;top:1600px}
.footer__links{left:0;width:876px;top:1692px;display:flex;justify-content:center;gap:27px;font-size:11px;color:var(--white)}
.footer__contact{left:0;width:876px;top:1722px;display:flex;justify-content:center;gap:22px;font-size:11px;color:var(--white)}
.footer__social{left:0;width:876px;top:1752px;display:flex;justify-content:center;gap:6px}
.footer__social span{width:9px;height:9px;border-radius:50%;background:var(--white)}
.footer__copy{left:0;width:876px;top:1797px;text-align:center;font-size:11px;color:var(--white)}
</style>
</head>
<body>

<!-- Home page -->
<section class="screen screen--home">
  <div class="abs brand"><span class="brand__mark"></span><span class="brand__name">Kestrel Therapy Member Registry</span></div>
  <div class="abs topbar topbar--email"><svg viewBox="0 0 16 16"><path d="M1 7l14-5-4 13-3-5z" fill="none" stroke="#2b5ca8"/></svg>EMAIL - info@ktmr-board.org</div>
  <div class="abs topbar topbar--call"><svg viewBox="0 0 16 16"><circle cx="8" cy="8" r="7" fill="none" stroke="#2b5ca8"/></svg>CALL US - <b>555.014.2600</b></div>
  <div class="abs get-started-btn">GET STARTED <svg width="8" height="6" viewBox="0 0 8 6"><path d="M1 1l3 3 3-3" fill="none" stroke="currentColor"/></svg></div>
  <div class="abs header-rule"></div>
  <nav class="abs nav"><span>HOME</span><span>CONTACT</span><span>COMPANY INFO</span><span>CHIROPRACTIC BOARDS</span><span>RESOURCES KTMR</span><span>SERVICES</span></nav>

  <svg class="abs hero" width="876" height="485" viewBox="0 0 876 485">
    <rect width="876" height="430" fill="url(#heroPhoto)" role="img" aria-label="Business team shaking hands around a meeting table"/>
    <defs><linearGradient id="heroPhoto" x1="0" y1="0" x2="1" y2="1"><stop offset="0" stop-color="#c9d3dc"/><stop offset=".5" stop-color="#7d8894"/><stop offset="1" stop-color="#2e3847"/></linearGradient></defs>
    <path d="M0 383H876V430Q438 540 0 430Z" fill="#2b5ca8" opacity=".92"/>
    <path d="M0 430Q438 540 876 430V485H0Z" fill="#fff"/>
  </svg>
  <span class="abs hero__dot is-active" style="top:275px"></span>
  <span class="abs hero__dot" style="top:293px"></span>
  <span class="abs hero__dot" style="top:312px"></span>
  <div class="abs hero__title">KTMR'S</div>
  <div class="abs hero__sub">94th Annual Business Meeting</div>
  <div class="abs hero__cta">READ MORE</div>

  <div class="abs mission__frame"></div>
  <div class="abs mission__photo" role="img" aria-label="Colleagues in discussion at a boardroom table"></div>
  <span class="abs point__icon" style="top:652px"></span>
  <div class="abs point__title" style="top:657px">OUR MISSION</div>
  <p class="abs point__text" style="top:692px">To protect the public by promoting excellence in chiropractic regulation through service to our member boards</p>
  <span class="abs point__icon" style="top:758px"></span>
  <div class="abs point__title" style="top:763px">OUR VISION</div>
  <p class="abs point__text" style="top:798px">The KTMR is the premier international resource for information and consolidated services for ensuring the safe, ethical practice of chiropractic</p>

  <h2 class="abs section-title">KTMR SERVICES - QUICKLINKS</h2>
  <svg class="abs arrow" style="left:50px" viewBox="0 0 16 32"><path d="M14 2L2 16l12 14" fill="none" stroke="#333" stroke-width="1.5"/></svg>
  <div class="abs quick" style="left:82px"><svg class="abs quick__badge" viewBox="0 0 86 98"><path d="M43 1L85 25V73L43 97L1 73V25Z" fill="#2b5ca8"/></svg><div class="quick__inner"><div class="quick__name">TEP-ROW - Therapist Event Portal - Registry of Warnings</div><div class="quick__desc">A repository of all chiropractic licensing boards' disciplinary actions</div></div></div>
  <div class="abs quick" style="left:322px"><svg class="abs quick__badge" viewBox="0 0 86 98"><path d="M43 1L85 25V73L43 97L1 73V25Z" fill="#2b5ca8"/></svg><div class="quick__inner"><div class="quick__name">MSDV - Member Spinal Desk Volunteers</div><div class="quick__desc">Professional recognition &amp; national certification</div></div></div>
  <div class="abs quick" style="left:563px"><svg class="abs quick__badge" viewBox="0 0 86 98"><path d="M43 1L85 25V73L43 97L1 73V25Z" fill="#2b5ca8"/></svg><div class="quick__inner"><div class="quick__name">ROVE - Registry of Vetted Ongoing Learning</div><div class="quick__desc">Search for courses or download a transcript</div></div></div>
  <svg class="abs arrow" style="left:812px" viewBox="0 0 16 32"><path d="M2 2l12 14L2 30" fill="none" stroke="#333" stroke-width="1.5"/></svg>

  <div class="abs members"></div>
  <h3 class="abs h-blue" style="left:69px;top:1318px">MEMBER ACCESS</h3>
  <div class="abs member-list"><p>Reset your password<br>Click a link below to log in</p><a>Register for meetings →</a><ul><li>Pay an Invoice</li><li>TEP-ROW</li><li>ROVE</li><li>MSDV</li><li>Report to TEP-ROW</li><li>DRVOM Login</li></ul></div>
  <span class="abs divider"></span>
  <h3 class="abs h-blue" style="left:303px;top:1318px">GET STARTED</h3>
  <div class="abs gs-card" style="left:305px"><div class="gs-card__head"><svg viewBox="0 0 24 24"><path d="M12 2l9 3v7c0 5-4 9-9 10-5-1-9-5-9-10V5z" fill="#2b5ca8"/></svg>REGULATORS</div><ul><li>Annual Meeting</li><li>District Meetings</li><li>Licensing Board Information</li><li>Library</li><li>Administrators(DRVOA)</li><li>Legal Advisers (DRVOM)</li><li>Other Chiropractic Organizations</li></ul></div>
  <div class="abs gs-card" style="left:483px"><div class="gs-card__head"><svg viewBox="0 0 24 24"><circle cx="9" cy="8" r="4" fill="none" stroke="#2b5ca8" stroke-width="1.6"/><path d="M2 21c0-5 14-5 14 0" fill="none" stroke="#2b5ca8" stroke-width="1.6"/><circle cx="16" cy="8" r="4" fill="none" stroke="#2b5ca8" stroke-width="1.6"/></svg>PUBLIC</div><ul><li>How to Check a License</li><li><a>Look up a License →</a></li><li>Request a Disciplinary Report</li><li>Consumer Information</li></ul></div>
  <div class="abs gs-card" style="left:661px"><div class="gs-card__head"><svg viewBox="0 0 24 24"><rect x="3" y="3" width="16" height="18" fill="none" stroke="#2b5ca8" stroke-width="1.6"/><path d="M6 8h10M6 12h8" stroke="#2b5ca8" stroke-width="1.4"/></svg>PROFESSIONALS</div><ul><li>Continuing Education Courses</li><li>Chiropractic Assistant Certification</li><li>View Your Continuing Ed Credits</li></ul></div>

  <svg class="abs footer" width="876" height="229" viewBox="0 0 876 229"><path d="M0 80Q438-30 876 80V229H0Z" fill="#2b5ca8"/></svg>
  <div class="abs footer__links"><span>Contact Us</span><span>Query TEP-ROW</span><span>Manage ROVE Courses</span><span>Pay Invoice</span><span>For Our Board</span></div>
  <div class="abs footer__contact"><span>⌖ 2280 Harlow Avenue, Suite 310</span><span>☏ 555.014.2600</span><span>✉ info@ktmr-board.org</span></div>
  <div class="abs footer__social"><span></span><span></span><span></span><span></span><span></span></div>
  <div class="abs footer__copy">© 2021 All Rights Reserved</div>
</section>

<!-- Home page with Get Started menu open -->
<section class="screen screen--menu">
  <div class="abs brand"><span class="brand__mark"></span><span class="brand__name">Kestrel Therapy Member Registry</span></div>
  <div class="abs topbar topbar--email"><svg viewBox="0 0 16 16"><path d="M1 7l14-5-4 13-3-5z" fill="none" stroke="#2b5ca8"/></svg>EMAIL - info@ktmr-board.org</div>
  <div class="abs topbar topbar--call"><svg viewBox="0 0 16 16"><circle cx="8" cy="8" r="7" fill="none" stroke="#2b5ca8"/></svg>CALL US - <b>555.014.2600</b></div>
  <div class="abs get-started-btn is-open">GET STARTED <svg width="8" height="6" viewBox="0 0 8 6"><path d="M1 1l3 3 3-3" fill="none" stroke="currentColor"/></svg></div>
  <div class="abs header-rule"></div>
  <nav class="abs nav"><span>HOME</span><span>CONTACT</span><span>COMPANY INFO</span><span>CHIROPRACTIC BOARDS</span><span>RESOURCES KTMR</span><span>SERVICES</span></nav>

  <svg class="abs hero" width="876" height="485" viewBox="0 0 876 485">
    <rect width="876" height="430" fill="url(#heroPhoto2)" role="img" aria-label="Business team shaking hands around a meeting table"/>
    <defs><linearGradient id="heroPhoto2" x1="0" y1="0" x2="1" y2="1"><stop offset="0" stop-color="#c9d3dc"/><stop offset=".5" stop-color="#7d8894"/><stop offset="1" stop-color="#2e3847"/></linearGradient></defs>
    <path d="M0 383H876V430Q438 540 0 430Z" fill="#2b5ca8" opacity=".92"/>
    <path d="M0 430Q438 540 876 430V485H0Z" fill="#fff"/>
  </svg>
  <span class="abs hero__dot is-active" style="top:275px"></span>
  <span class="abs hero__dot" style="top:293px"></span>
  <span class="abs hero__dot" style="top:312px"></span>
  <div class="abs hero__title">KTMR'S</div>
  <div class="abs hero__sub">94th Annual Business Meeting</div>
  <div class="abs hero__cta">READ MORE</div>

  <div class="abs mega">
    <ul class="mega__col1"><li>Chiropractic Regulators</li><li>Annual Meeting</li><li>District Meetings</li><li>Licensing Board Information</li><li>Library</li><li>Administrators ( DRVOM )</li><li>Legal Advisors ( DRVOM )</li><li>Other Chiropractic Organizations</li></ul>
    <ul class="mega__col2"><li>Chiropractic Patients</li><li>How to Check a license</li><li>Look up a license</li><li>Request a Disciplinary Report</li><li>Consumer Information</li></ul>
    <ul class="mega__col3"><li>Registered Chiropractors &amp;</li><li class="mega__indent">Chiropractic Assistants</li><li>Coninuing Education Courses</li><li>Chiropractic Assistant</li><li>Certification</li><li>View Your Continuing Ed Credits</li></ul>
  </div>

  <div class="abs mission__frame"></div>
  <div class="abs mission__photo" role="img" aria-label="Colleagues in discussion at a boardroom table"></div>
  <span class="abs point__icon" style="top:652px"></span>
  <div class="abs point__title" style="top:657px">OUR MISSION</div>
  <p class="abs point__text" style="top:692px">To protect the public by promoting excellence in chiropractic regulation through service to our member boards</p>
  <span class="abs point__icon" style="top:758px"></span>
  <div class="abs point__title" style="top:763px">OUR VISION</div>
  <p class="abs point__text" style="top:798px">The KTMR is the premier international resource for information and consolidated services for ensuring the safe, ethical practice of chiropractic</p>

  <h2 class="abs section-title">KTMR SERVICES - QUICKLINKS</h2>
  <svg class="abs arrow" style="left:50px" viewBox="0 0 16 32"><path d="M14 2L2 16l12 14" fill="none" stroke="#333" stroke-width="1.5"/></svg>
  <div class="abs quick" style="left:82px"><svg class="abs quick__badge" viewBox="0 0 86 98"><path d="M43 1L85 25V73L43 97L1 73V25Z" fill="#2b5ca8"/></svg><div class="quick__inner"><div class="quick__name">TEP-ROW - Therapist Event Portal - Registry of Warnings</div><div class="quick__desc">A repository of all chiropractic licensing boards' disciplinary actions</div></div></div>
  <div class="abs quick" style="left:322px"><svg class="abs quick__badge" viewBox="0 0 86 98"><path d="M43 1L85 25V73L43 97L1 73V25Z" fill="#2b5ca8"/></svg><div class="quick__inner"><div class="quick__name">MSDV - Member Spinal Desk Volunteers</div><div class="quick__desc">Professional recognition &amp; national certification</div></div></div>
  <div class="abs quick" style="left:563px"><svg class="abs quick__badge" viewBox="0 0 86 98"><path d="M43 1L85 25V73L43 97L1 73V25Z" fill="#2b5ca8"/></svg><div class="quick__inner"><div class="quick__name">ROVE - Registry of Vetted Ongoing Learning</div><div class="quick__desc">Search for courses or download a transcript</div></div></div>
  <svg class="abs arrow" style="left:812px" viewBox="0 0 16 32"><path d="M2 2l12 14L2 30" fill="none" stroke="#333" stroke-width="1.5"/></svg>

  <div class="abs members"></div>
  <h3 class="abs h-blue" style="left:69px;top:1318px">MEMBER ACCESS</h3>
  <div class="abs member-list"><p>Reset your password<br>Click a link below to log in</p><a>Register for meetings →</a><ul><li>Pay an Invoice</li><li>TEP-ROW</li><li>ROVE</li><li>MSDV</li><li>Report to TEP-ROW</li><li>DRVOM Login</li></ul></div>
  <span class="abs divider"></span>
  <h3 class="abs h-blue" style="left:303px;top:1318px">GET STARTED</h3>
  <div class="abs gs-card" style="left:305px"><div class="gs-card__head"><svg viewBox="0 0 24 24"><path d="M12 2l9 3v7c0 5-4 9-9 10-5-1-9-5-9-10V5z" fill="#2b5ca8"/></svg>REGULATORS</div><ul><li>Annual Meeting</li><li>District Meetings</li><li>Licensing Board Information</li><li>Library</li><li>Administrators(DRVOA)</li><li>Legal Advisers (DRVOM)</li><li>Other Chiropractic Organizations</li></ul></div>
  <div class="abs gs-card" style="left:483px"><div class="gs-card__head"><svg viewBox="0 0 24 24"><circle cx="9" cy="8" r="4" fill="none" stroke="#2b5ca8" stroke-width="1.6"/><path d="M2 21c0-5 14-5 14 0" fill="none" stroke="#2b5ca8" stroke-width="1.6"/><circle cx="16" cy="8" r="4" fill="none" stroke="#2b5ca8" stroke-width="1.6"/></svg>PUBLIC</div><ul><li>How to Check a License</li><li><a>Look up a License →</a></li><li>Request a Disciplinary Report</li><li>Consumer Information</li></ul></div>
  <div class="abs gs-card" style="left:661px"><div class="gs-card__head"><svg viewBox="0 0 24 24"><rect x="3" y="3" width="16" height="18" fill="none" stroke="#2b5ca8" stroke-width="1.6"/><path d="M6 8h10M6 12h8" stroke="#2b5ca8" stroke-width="1.4"/></svg>PROFESSIONALS</div><ul><li>Continuing Education Courses</li><li>Chiropractic Assistant Certification</li><li>View Your Continuing Ed Credits</li></ul></div>

  <svg class="abs footer" width="876" height="229" viewBox="0 0 876 229"><path d="M0 80Q438-30 876 80V229H0Z" fill="#2b5ca8"/></svg>
  <div class="abs footer__links"><span>Contact Us</span><span>Query TEP-ROW</span><span>Manage ROVE Courses</span><span>Pay Invoice</span><span>For Our Board</span></div>
  <div class="abs footer__contact"><span>⌖ 2280 Harlow Avenue, Suite 310</span><span>☏ 555.014.2600</span><span>✉ info@ktmr-board.org</span></div>
  <div class="abs footer__social"><span></span><span></span><span></span><span></span><span></span></div>
  <div class="abs footer__copy">© 2021 All Rights Reserved</div>
</section>

</body>
</html>
```